Marlow Vale Stud website

We would like to create a horse stud/agistment farm website similar to this websites we have attached below:
www.thornbeck.com.au
www.quillstead.com.au
www.brackley.com
www.pimsey.com.au
The main colour scheme are purple and white to align with the stable's racing colours.
We have also attach the company logo and also images of the farm and create some ideas for the website.
Many thanks for looking into this project!

```html
<!DOCTYPE html>
<html lang="en">
<head>
<meta charset="utf-8">
<title>Marlow Vale Stud</title>
<link href="https://fonts.googleapis.com/css2?family=Montserrat:wght@500;600;700&family=Open+Sans:wght@400;600&display=swap" rel="stylesheet">
<style>
:root{
  --purple:#4a1942;
  --purple-dark:#3a1234;
  --purple-band:#4f2450;
  --ink:#1e1e1e;
  --body:#6b6b6b;
  --grey-bg:#f4f4f4;
  --line:#c9c9c9;
  --white:#ffffff;
}
*{box-sizing:border-box;margin:0;padding:0}
html,body{width:1200px;height:4615px;overflow:hidden}
body{font-family:"Open Sans",sans-serif;color:var(--body);background:var(--white);position:relative}
.abs{position:absolute}
h1,h2,h3,h4,.brand,.btn,.nav a{font-family:"Montserrat",sans-serif}
.btn{position:absolute;display:flex;align-items:center;justify-content:center;font-size:26px;font-weight:500;color:var(--white);background:var(--purple)}
.btn.outline{background:transparent;border:2px solid var(--white)}
.photo{position:absolute}

/* header */
.site-header{position:absolute;left:0;top:0;width:1200px;height:105px;background:var(--purple)}
.brand{position:absolute;display:flex;align-items:center;gap:14px;color:var(--white);font-weight:700}
.brand .dot{border-radius:50%;border:0;background:var(--white)}
.site-header .brand{left:108px;top:28px;font-size:31px}
.site-header .brand .dot{width:44px;height:44px}
.nav{position:absolute;right:92px;top:40px;display:flex;gap:22px}
.nav a{color:var(--white);text-decoration:none;font-size:18px;font-weight:700}

/* hero */
.hero{position:absolute;left:0;top:105px;width:1200px;height:640px;background:linear-gradient(180deg,#3c3a33 0%,#5f5c50 35%,#6b7a55 60%,#8a3f62 82%,#4f6b3e 100%)}
.hero h1{position:absolute;left:0;width:1200px;top:240px;text-align:center;color:var(--white);font-size:54px;font-weight:700}
.hero p{position:absolute;left:270px;width:660px;top:322px;text-align:center;color:var(--white);font-size:17px;line-height:28px}
.hero .arrow{position:absolute;top:318px;width:34px;height:34px;border-radius:50%;background:var(--white)}
.hero .arrow svg{position:absolute;left:9px;top:9px}
.hero .btn{left:492px;top:403px;width:219px;height:55px}
.tear{position:absolute;left:0;width:1200px}

/* about */
.about-photo{left:92px;top:846px;width:333px;height:333px;border-radius:50%;border:5px solid var(--purple);background:linear-gradient(180deg,#5d8fd0 0%,#9ec2e8 45%,#5a4a3a 62%,#6f9a45 80%)}
.section-title{position:absolute;color:var(--purple);font-size:43px;font-weight:700}
.about h2{left:486px;top:838px}
.about p{position:absolute;left:486px;width:594px;top:905px;font-size:17px;line-height:31px}
.about .btn{left:483px;top:1138px;width:191px;height:56px}

/* stallions */
.stallions{position:absolute;left:0;top:1335px;width:1200px;height:555px;background:linear-gradient(180deg,var(--purple-band) 0%,#5a2d58 50%,#4a1f47 100%)}
.stallions h2{left:0;width:1200px;text-align:center;top:64px;color:var(--white)}
.stallion{position:absolute;top:206px;width:246px}
.stallion .photo{position:relative;width:246px;height:154px;background:linear-gradient(180deg,#3c4d2c 0%,#5e4030 55%,#6a8d3c 100%)}
.stallion h4{margin-top:18px;text-align:center;color:var(--white);font-size:20px;font-weight:700}
.stallions .btn{left:505px;top:450px;width:190px;height:55px}

/* portfolio */
.portfolio h2{left:0;width:1200px;text-align:center;top:1990px}
.tile{position:absolute;background:linear-gradient(160deg,#5b6a42,#7f6a52)}
.zoom{position:absolute;left:50%;top:50%;transform:translate(-50%,-50%)}

/* news */
.news{position:absolute;left:0;top:2748px;width:1200px;height:747px;background:var(--grey-bg)}
.news h2{left:0;width:1200px;text-align:center;top:70px}
.news-feature{position:absolute;left:89px;top:175px;width:480px;height:292px;background:linear-gradient(180deg,#2f4a2a 0%,#557a3a 55%,#7ea44d 100%)}
.news-feature-title{position:absolute;left:92px;top:492px;color:var(--ink);font-size:23px;font-weight:700}
.meta{position:absolute;display:flex;align-items:center;gap:10px;font-size:15px;color:var(--body)}
.meta span{display:flex;align-items:center;gap:8px;margin-right:32px}
.news .excerpt{position:absolute;font-size:16px;line-height:28px}
.news-item .photo{left:625px;width:153px;height:126px;background:linear-gradient(180deg,#3f5a2f,#6a4a34 60%,#6f9a45)}
.news-item h3{position:absolute;left:797px;color:var(--ink);font-size:18px;font-weight:700}

/* contact */
.contact h2{left:0;width:1200px;text-align:center;top:3572px}
.field{position:absolute;height:40px;border:1.5px solid var(--line);border-radius:6px;font-size:13px;color:#555;padding:10px 12px}
.contact .btn{left:495px;top:3948px;width:191px;height:55px}

/* footer */
.site-footer{position:absolute;left:0;top:4092px;width:1200px;height:523px;background:linear-gradient(180deg,#4a1f47 0%,var(--purple-dark) 100%)}
.site-footer .brand{left:92px;top:182px;font-size:36px}
.site-footer .brand .dot{width:56px;height:56px}
.site-footer .about-text{position:absolute;left:100px;top:258px;width:380px;color:var(--white);font-size:17px;line-height:28px}
.site-footer h4{position:absolute;top:176px;color:var(--white);font-size:29px;font-weight:600}
.links{position:absolute;left:526px;top:238px;list-style:none}
.links li{color:var(--white);font-size:16px;line-height:26.5px}
.news-text{position:absolute;left:822px;top:232px;width:290px;color:var(--white);font-size:14px;line-height:22px}
.news-input{position:absolute;left:822px;top:306px;width:228px;height:35px;background:var(--white);border-radius:4px;font-size:12px;color:#666;padding:10px 12px}
.send{position:absolute;left:822px;top:353px;width:118px;height:40px;border:1.5px solid var(--white);border-radius:3px;color:var(--white);font-size:17px;display:flex;align-items:center;justify-content:center}
.copyright{position:absolute;left:92px;top:466px;color:var(--white);font-size:17px}
.social{position:absolute;left:905px;top:466px;display:flex;gap:18px}
.social i{display:block;width:20px;height:20px;background:var(--white);border-radius:3px}
</style>
</head>
<body>

<header class="site-header">
  <div class="brand"><span class="dot"></span>Marlow Vale Stud</div>
  <nav class="nav"><a>Home</a><a>About Us</a><a>Stallions</a><a>Farm</a><a>Portfolio</a><a>Contact Us</a></nav>
</header>

<section class="hero" role="img" aria-label="Jockey in purple silks riding a grey racehorse past flower beds">
  <h1>Welcome to Marlow Vale Stud</h1>
  <p>Lorem ipsum dolor sit amet, consectetur adipiscing elit. Etiam aliquam erat in velit blandit, faucibus feugiat nisi ultricies. Maecenas blandit est nulla,</p>
  <div class="arrow" style="left:30px"><svg width="16" height="16" viewBox="0 0 16 16"><path d="M10 3 5 8l5 5" fill="none" stroke="#222" stroke-width="2.4"/></svg></div>
  <div class="arrow" style="left:1130px"><svg width="16" height="16" viewBox="0 0 16 16"><path d="M6 3l5 5-5 5" fill="none" stroke="#222" stroke-width="2.4"/></svg></div>
  <div class="btn">View More</div>
</section>
<svg class="tear" style="top:660px" width="1200" height="90" viewBox="0 0 1200 90" preserveAspectRatio="none">
  <path d="M0 40 L60 52 120 44 180 60 240 50 300 66 360 48 420 58 480 42 540 54 600 38 660 52 720 40 780 50 840 34 900 46 960 30 1020 44 1080 28 1140 40 1200 26 L1200 90 L0 90Z" fill="#fff"/>
</svg>

<section class="about">
  <div class="photo about-photo" role="img" aria-label="Three horses standing in a green paddock under blue sky"></div>
  <h2 class="section-title">About Us</h2>
  <p>Lorem ipsum dolor sit amet, consectetur adipiscing elit. Etiam aliquam erat in velit blandit, faucibus feugiat nisi ultricies. Maecenas blandit est nulla, nec finibus massa facilisis iaculis. Sed ac enim vel lectus dictum cursus at id mauris. Nullam arcu nunc, lacinia et finibus sed, nec finibus massa facilisis iaculis. Sed ac enim vel lectus dictum cursus at id mauris. Nullam arcu nunc, lacinia et finibus sed,</p>
  <div class="btn">Read More</div>
</section>

<section class="stallions" role="region" aria-label="Stallions">
  <h2 class="section-title">Stallions</h2>
  <div class="stallion" style="left:95px"><div class="photo" role="img" aria-label="Dark stallion standing side-on"></div><h4>Silverline</h4></div>
  <div class="stallion" style="left:351px"><div class="photo" role="img" aria-label="Bay stallion standing side-on"></div><h4>Harbour Stone</h4></div>
  <div class="stallion" style="left:607px"><div class="photo" role="img" aria-label="Bay stallion on grass"></div><h4>Granite</h4></div>
  <div class="stallion" style="left:862px"><div class="photo" role="img" aria-label="Chestnut stallion on grass"></div><h4>Sandpiper Trail</h4></div>
  <div class="btn outline">View More</div>
</section>

<section class="portfolio">
  <h2 class="section-title">Portfolio</h2>
  <div class="tile" style="left:120px;top:2101px;width:470px;height:351px;background:linear-gradient(160deg,#2b3b5a,#b8b0a6 55%,#3a3a3a)" role="img" aria-label="Grey racehorse with handlers at presentation"></div>
  <div class="tile" style="left:597px;top:2101px;width:240px;height:177px;background:#3e3a32" role="img" aria-label="Stud building behind garden">
    <svg class="zoom" width="52" height="52" viewBox="0 0 52 52"><circle cx="22" cy="22" r="15" fill="none" stroke="#fff" stroke-width="4"/><path d="M33 33l13 13M22 15v14M15 22h14" stroke="#fff" stroke-width="4"/></svg>
  </div>
  <div class="tile" style="left:843px;top:2101px;width:231px;height:177px;background:linear-gradient(180deg,#5c7a3a,#7a5a3e)" role="img" aria-label="Horse grazing"></div>
  <div class="tile" style="left:597px;top:2284px;width:240px;height:168px;background:linear-gradient(180deg,#6a7a6a,#7d9a3a)" role="img" aria-label="Green paddock"></div>
  <div class="tile" style="left:843px;top:2284px;width:231px;height:168px;background:linear-gradient(180deg,#7aa0d8,#4a3e30 60%,#6a9a40)" role="img" aria-label="Horses in a field"></div>
  <div class="tile" style="left:120px;top:2461px;width:228px;height:185px;background:linear-gradient(180deg,#3a5a2a,#6a8a3a)" role="img" aria-label="Hedge-lined driveway"></div>
  <div class="tile" style="left:354px;top:2461px;width:480px;height:185px;background:linear-gradient(160deg,#1f2a4a,#6a3a7a 50%,#8a8a8a)" role="img" aria-label="Jockey in purple silks on horse"></div>
  <div class="tile" style="left:840px;top:2461px;width:234px;height:185px;background:linear-gradient(180deg,#7a8a6a,#5a3e2e)" role="img" aria-label="Mare and foal"></div>
</section>

<section class="news">
  <h2 class="section-title">News</h2>
  <div class="news-feature" role="img" aria-label="Chestnut horse standing on lawn before trees"></div>
  <h3 class="news-feature-title">Hooked On Quiet Verdict</h3>
  <div class="meta" style="left:97px;top:545px">
    <span><svg width="16" height="16" viewBox="0 0 16 16"><circle cx="8" cy="5" r="3.2" fill="none" stroke="#555" stroke-width="1.5"/><path d="M2 15c0-3.5 2.7-5.5 6-5.5s6 2 6 5.5" fill="none" stroke="#555" stroke-width="1.5"/></svg>Kestrel</span>
    <span><svg width="16" height="16" viewBox="0 0 16 16"><rect x="1.5" y="3" width="13" height="11.5" fill="none" stroke="#555" stroke-width="1.5"/><path d="M1.5 7h13M5 1v4M11 1v4" stroke="#555" stroke-width="1.5"/></svg>Mar 10, 2019</span>
  </div>
  <p class="excerpt" style="left:92px;top:583px;width:480px">Lorem ipsum dolor sit amet, consectetur adipiscing elit. Etiam aliquam erat in velit blandit, faucibus feugiat nisi ultricies. Maecenas blandit est nulla</p>

  <div class="news-item">
    <div class="photo" style="top:172px" role="img" aria-label="Chestnut horse in paddock"></div>
    <h3 style="top:172px">Eyes On Black-Type At Linfield</h3>
    <div class="meta" style="left:800px;top:210px"><span>&#9675; Kestrel</span><span>&#9634; Mar 10, 2019</span></div>
    <p class="excerpt" style="left:797px;top:236px;width:300px;font-size:15px;line-height:22px">Lorem ipsum dolor sit amet, consectetur adipiscing elit. Etiam aliquam erat in velit blandit, faucibus feugiat nisi ultricies.</p>
  </div>
  <div class="news-item">
    <div class="photo" style="top:341px" role="img" aria-label="Horse grazing near trees"></div>
    <h3 style="top:341px">Quiet Verdict'S Premier</h3>
    <div class="meta" style="left:800px;top:379px"><span>&#9675; Kestrel</span><span>&#9634; Mar 10, 2019</span></div>
    <p class="excerpt" style="left:797px;top:405px;width:300px;font-size:15px;line-height:22px">Lorem ipsum dolor sit amet, adipiscing elit. Etiam aliquam erat in velit blandit, faucibus feugiat nisi</p>
  </div>
  <div class="news-item">
    <div class="photo" style="top:514px" role="img" aria-label="Bay horse standing in paddock"></div>
    <h3 style="top:514px">Thornbeck'S 2019 Harrowgate Premier</h3>
    <div class="meta" style="left:800px;top:552px"><span>&#9675; Kestrel</span><span>&#9634; Mar 10, 2019</span></div>
    <p class="excerpt" style="left:797px;top:578px;width:300px;font-size:15px;line-height:22px">Lorem ipsum dolor sit amet, consectetur adipiscing elit. Etiam aliquam erat in velit blandit, faucibus</p>
  </div>
</section>

<section class="contact">
  <h2 class="section-title">Contact Us</h2>
  <div class="field" style="left:126px;top:3680px;width:459px">Name</div>
  <div class="field" style="left:612px;top:3680px;width:459px">Last Name</div>
  <div class="field" style="left:126px;top:3732px;width:459px">Email</div>
  <div class="field" style="left:612px;top:3732px;width:459px">Phone Number</div>
  <div class="field" style="left:126px;top:3788px;width:945px;height:110px">Messages</div>
  <div class="btn">Submit</div>
</section>

<svg class="tear" style="top:4050px" width="1200" height="50" viewBox="0 0 1200 50" preserveAspectRatio="none">
  <path d="M0 24 L70 14 140 26 210 12 280 22 350 8 420 20 490 10 560 22 630 6 700 18 770 8 840 22 910 12 980 24 1050 10 1120 20 1200 12 L1200 50 L0 50Z" fill="#4a1f47"/>
</svg>
<footer class="site-footer">
  <div class="brand"><span class="dot"></span>Marlow Vale Stud</div>
  <p class="about-text">Lorem ipsum dolor sit amet, consectetur adipiscing elit. Etiam aliquam erat in velit blandit, faucibus feugiat nisi ultricies.</p>
  <h4 style="left:526px">Quick Links</h4>
  <ul class="links"><li>Home</li><li>About Us</li><li>Stallions</li><li>Farm</li><li>Portfolio</li><li>Contact Us</li></ul>
  <h4 style="left:822px">NewsLetter</h4>
  <p class="news-text">Lorem ipsum dolor sit amet, consectetur adipiscing elit.</p>
  <div class="news-input">Enter the Email</div>
  <div class="send">Send</div>
  <p class="copyright">© 2019 Marlow Vale Stud. All Rights Reserved</p>
  <div class="social"><i></i><i></i><i></i><i></i><i></i><i></i></div>
</footer>

</body>
</html>
```